IT Company that provides secure IT solutions and services to our customers

We need business cards and a logo for a new IT Solutions company just created based in Kuala Lumpur, Malaysia. But will also be serving other countries in the region. We provide secure data, voice solutions on mobile platforms. Our first offering is encrypted voice and data solutions for IOS, Android, Windows and BlackBerry devices.

Target Market(s)

large organizations Govt, Police, Defence, Anti-corruption, Legal, highly regulated industries such as Health-care, Financial, Banking, Insurance,

Industry/Entity Type

Information Technology

Contact Information for Business Card

VelmoraNet (Logo - colour is ORVEX blue)Roshan Adeel Managing Director Kryption IT Sdn. Bhd.5th Floor, Block D, Wisma PLB,No.14 Jalan Seri Melor,50470, Kuala LumpurMalaysia

Font styles to use
Sans Serif

Colors
3176b5
ec1f27
fbed22

Requirements
Must have
• VelmoraNet all in Blue like ORVEX blue. A logo design perhaps a play of VN, K with a dangling T (colour can be any)
Nice to have
• I want a clean crisp card, not too busy, easy to read.

```html
<!DOCTYPE html>
<html lang="en">
<head>
<meta charset="utf-8">
<title>VelmoraNet Business Card</title>
<link rel="stylesheet" href="https://fonts.googleapis.com/css2?family=Raleway:wght@500&family=Source+Sans+3:wght@400;700&display=swap">
<style>
  :root {
    --backdrop: #151515;
    --card-light: #f3f3f3;
    --card-blue: #1a5aab;
    --brand-blue: #1b57a8;
    --ink: #1e1e1e;
    --mark-grey: #444444;
    --white: #ffffff;
    --emboss: rgba(255, 255, 255, 0.08);
  }
  html, body {
    margin: 0;
    padding: 0;
    width: 1200px;
    height: 900px;
    overflow: hidden;
    background: var(--backdrop);
  }
  .stage {
    position: relative;
    width: 1200px;
    height: 900px;
  }
  .card {
    position: absolute;
    top: 184px;
    height: 490px;
    border-radius: 12px;
    overflow: hidden;
  }
  .card--front {
    left: 299px;
    width: 301px;
    background: var(--card-light);
    text-align: center;
  }
  .card--back {
    left: 645px;
    width: 304px;
    background: var(--card-blue);
  }
  .brand-circle {
    position: absolute;
    left: 118px;
    top: 33px;
    width: 56px;
    height: 56px;
    border: 2.5px solid var(--mark-grey);
    border-radius: 50%;
  }
  .wordmark {
    font-family: "Raleway", sans-serif;
    font-weight: 500;
    letter-spacing: 0.2px;
    margin: 0;
    white-space: nowrap;
  }
  .card--front .wordmark {
    position: absolute;
    left: 0;
    right: 0;
    top: 98px;
    font-size: 47px;
    line-height: 60px;
    color: var(--brand-blue);
  }
  .contact {
    position: absolute;
    left: 0;
    right: 0;
    top: 303px;
    font-family: "Source Sans 3", sans-serif;
    color: var(--ink);
  }
  .contact__name,
  .contact__company {
    font-weight: 700;
    font-size: 15px;
    line-height: 18px;
    color: var(--brand-blue);
    margin: 0;
  }
  .contact__role {
    font-size: 13.5px;
    line-height: 18px;
    margin: 0 0 34px;
  }
  .contact__address {
    font-size: 13.5px;
    line-height: 18px;
    margin: 0;
    font-style: normal;
  }
  .back-circle {
    position: absolute;
    left: -30px;
    top: 12px;
    width: 340px;
    height: 340px;
    border: 3px solid var(--emboss);
    border-radius: 50%;
  }
  .card--back .wordmark {
    position: absolute;
    left: 0;
    right: 0;
    top: 386px;
    text-align: center;
    font-size: 49px;
    line-height: 60px;
    color: var(--white);
  }
</style>
</head>
<body>
  <main class="stage">
    <section class="card card--front" aria-label="Business card front">
      <div class="brand-circle"></div>
      <h1 class="wordmark">VelmoraNet</h1>
      <div class="contact">
        <p class="contact__name">ROSHAN ADEEL</p>
        <p class="contact__role">Managing Director</p>
        <p class="contact__company">VELMORA NET</p>
        <address class="contact__address">
          Sdn. Bhd.5th Floor, Block D,&nbsp; Wisma<br>
          PLB,No.14 Jalan Seri Melor, 50470,<br>
          Kuala Lumpur Malaysia
        </address>
      </div>
    </section>
    <section class="card card--back" aria-label="Business card back">
      <div class="back-circle"></div>
      <p class="wordmark">VelmoraNet</p>
    </section>
  </main>
</body>
</html>
```